Step and Repeat Backdrop for wedding reception photo booth

Would like to have a Step and Repeat Backdrop (8 foot high by 10 foot wide) that incorporates the wedding logo (attached) and the names Helen and Gavin. Background should be white, and wedding colors are burgundy and gold. Show me creativity :-) I have included some random samples.

```html
<!DOCTYPE html>
<html lang="en">
<head>
<meta charset="utf-8">
<title>Helen and Gavin — Step and Repeat Backdrop</title>
<link rel="stylesheet" href="https://fonts.googleapis.com/css2?family=Cinzel:wght@400;600&display=swap">
<style>
  :root {
    --paper: #ffffff;
    --gold: #bf8c1c;
    --burgundy: #9c1f45;
  }
  html, body {
    margin: 0;
    padding: 0;
    width: 766px;
    height: 1200px;
    overflow: hidden;
    background: var(--paper);
  }
  .canvas {
    position: relative;
    width: 766px;
    height: 1200px;
    background: var(--paper);
    overflow: hidden;
  }
  .backdrop {
    position: absolute;
    left: 0;
    top: 302px;
    width: 720px;
    height: 560px;
    transform: scale(1.0639);
    transform-origin: 0 0;
    background: var(--paper);
    font-family: "Cinzel", serif;
  }
  .tile-mark {
    position: absolute;
    width: 50px;
    height: 40px;
    margin-left: -25px;
    margin-top: -20px;
    display: flex;
    flex-direction: column;
    align-items: center;
    justify-content: center;
    color: var(--gold);
    font-weight: 600;
    font-size: 7px;
    line-height: 1.15;
    letter-spacing: 0.3px;
    text-align: center;
  }
  .tile-label {
    position: absolute;
    margin-top: -4px;
    color: var(--gold);
    font-weight: 600;
    font-size: 6.5px;
    letter-spacing: 0.2px;
    white-space: nowrap;
  }
  .hero-mark {
    position: absolute;
    left: 220px;
    top: 120px;
    width: 280px;
    height: 270px;
    display: flex;
    flex-direction: column;
    align-items: center;
    justify-content: center;
    gap: 4px;
    color: var(--gold);
    font-weight: 600;
    font-size: 46px;
    line-height: 1.05;
    text-align: center;
  }
  .hero-mark .dot {
    width: 12px;
    height: 12px;
    border-radius: 50%;
    background: var(--gold);
    margin-bottom: 8px;
  }
  .hero-names {
    position: absolute;
    left: 150px;
    width: 420px;
    top: 388px;
    text-align: center;
    color: var(--burgundy);
    font-weight: 400;
    font-size: 33px;
    letter-spacing: 0.5px;
    white-space: nowrap;
  }
</style>
</head>
<body>
<main class="canvas">
  <section class="backdrop" aria-label="Helen and Gavin step and repeat backdrop">

    <!-- row 1 -->
    <div class="tile-mark" style="left:55px;top:40px"><span>Helen</span><span>&amp;</span><span>Gavin</span></div>
    <div class="tile-label" style="left:104px;top:40px">HELEN AND GAVIN</div>
    <div class="tile-mark" style="left:316px;top:40px"><span>Helen</span><span>&amp;</span><span>Gavin</span></div>
    <div class="tile-label" style="left:365px;top:40px">HELEN AND GAVIN</div>
    <div class="tile-mark" style="left:578px;top:40px"><span>Helen</span><span>&amp;</span><span>Gavin</span></div>
    <div class="tile-label" style="left:627px;top:40px">HELEN AND GAVIN</div>

    <!-- row 2 -->
    <div class="tile-mark" style="left:186px;top:100px"><span>Helen</span><span>&amp;</span><span>Gavin</span></div>
    <div class="tile-label" style="left:234px;top:100px">HELEN AND GAVIN</div>
    <div class="tile-mark" style="left:447px;top:100px"><span>Helen</span><span>&amp;</span><span>Gavin</span></div>
    <div class="tile-label" style="left:496px;top:100px">HELEN AND GAVIN</div>

    <!-- row 3 -->
    <div class="tile-mark" style="left:55px;top:160px"><span>Helen</span><span>&amp;</span><span>Gavin</span></div>
    <div class="tile-label" style="left:104px;top:160px">HELEN AND GAVIN</div>
    <div class="tile-mark" style="left:578px;top:160px"><span>Helen</span><span>&amp;</span><span>Gavin</span></div>
    <div class="tile-label" style="left:627px;top:160px">HELEN AND GAVIN</div>

    <!-- row 4 -->
    <div class="tile-mark" style="left:186px;top:220px"><span>Helen</span><span>&amp;</span><span>Gavin</span></div>
    <div class="tile-label" style="left:496px;top:220px">HELEN AND GAVIN</div>

    <!-- row 5 -->
    <div class="tile-mark" style="left:55px;top:280px"><span>Helen</span><span>&amp;</span><span>Gavin</span></div>
    <div class="tile-label" style="left:104px;top:280px">HELEN AND GAVIN</div>
    <div class="tile-mark" style="left:578px;top:280px"><span>Helen</span><span>&amp;</span><span>Gavin</span></div>
    <div class="tile-label" style="left:627px;top:280px">HELEN AND GAVIN</div>

    <!-- row 6 -->
    <div class="tile-mark" style="left:186px;top:340px"><span>Helen</span><span>&amp;</span><span>Gavin</span></div>
    <div class="tile-label" style="left:496px;top:340px">HELEN AND GAVIN</div>

    <!-- row 7 -->
    <div class="tile-mark" style="left:55px;top:400px"><span>Helen</span><span>&amp;</span><span>Gavin</span></div>
    <div class="tile-label" style="left:104px;top:400px">HELEN AND GAVIN</div>
    <div class="tile-mark" style="left:578px;top:400px"><span>Helen</span><span>&amp;</span><span>Gavin</span></div>
    <div class="tile-label" style="left:627px;top:400px">HELEN AND GAVIN</div>

    <!-- row 8 -->
    <div class="tile-mark" style="left:186px;top:460px"><span>Helen</span><span>&amp;</span><span>Gavin</span></div>
    <div class="tile-label" style="left:234px;top:460px">HELEN AND GAVIN</div>
    <div class="tile-mark" style="left:447px;top:460px"><span>Helen</span><span>&amp;</span><span>Gavin</span></div>
    <div class="tile-label" style="left:496px;top:460px">HELEN AND GAVIN</div>

    <!-- row 9 -->
    <div class="tile-mark" style="left:55px;top:520px"><span>Helen</span><span>&amp;</span><span>Gavin</span></div>
    <div class="tile-label" style="left:104px;top:520px">HELEN AND GAVIN</div>
    <div class="tile-mark" style="left:316px;top:520px"><span>Helen</span><span>&amp;</span><span>Gavin</span></div>
    <div class="tile-label" style="left:365px;top:520px">HELEN AND GAVIN</div>
    <div class="tile-mark" style="left:578px;top:520px"><span>Helen</span><span>&amp;</span><span>Gavin</span></div>
    <div class="tile-label" style="left:627px;top:520px">HELEN AND GAVIN</div>

    <!-- centre feature -->
    <div class="hero-mark">
      <span class="dot"></span>
      <span>Helen</span>
      <span>&amp; Gavin</span>
    </div>
    <h1 class="hero-names" style="margin:0">HELEN AND GAVIN</h1>

  </section>
</main>
</body>
</html>
```